Website re-design for Brightmoor LLC website ( has existing website )

Looking to do a complete re-design of Brightmoorllc. The existing website is dated and built in wordpress. The new website will not be wordpress. The project folder includes an overview.txt file with details on the project. The file also contains a list of websites that he/she likes which I am sure is very helpful .
Number of Pages Required
1 page

```html
<!DOCTYPE html>
<html lang="en">
<head>
<meta charset="utf-8">
<title>Brightmoor LLC – Lake Weed Removal</title>
<link href="https://fonts.googleapis.com/css2?family=Poppins:wght@400;500;600;700&family=Roboto:wght@400;500;700&display=swap" rel="stylesheet">
<style>
:root{
  --blue:#1d5bb0;
  --blue-dark:#0f3f86;
  --navy:#0a2a5e;
  --ink:#1a1a1a;
  --text:#555;
  --grey-bg:#efefee;
  --footer:#050505;
  --white:#fff;
}
*{margin:0;padding:0;box-sizing:border-box}
html,body{width:1200px;height:4736px;overflow:hidden}
body{position:relative;background:var(--white);font-family:"Roboto",Arial,sans-serif;color:var(--text)}
.abs{position:absolute}
.h2{position:absolute;left:0;width:1200px;text-align:center;font-family:"Poppins",sans-serif;font-weight:700;font-size:68px;color:var(--ink);line-height:1}
.rule{position:absolute;left:520px;width:160px;height:4px;background:var(--blue)}
.arrow{position:absolute;width:30px;height:30px}
.btn{position:absolute;display:flex;align-items:center;justify-content:center;border-radius:30px;font-family:"Poppins",sans-serif;font-weight:600;font-size:13px}

/* header */
.topline{top:0;left:0;width:1200px;height:5px;background:var(--blue)}
.brand{top:32px;left:112px;display:flex;flex-direction:column;gap:6px}
.brand-name{font-family:"Poppins",sans-serif;font-weight:600;font-size:38px;color:var(--ink);line-height:1;letter-spacing:.5px}
.brand-tag{font-family:"Poppins",sans-serif;font-size:11px;font-weight:500;color:#666;white-space:nowrap}
.follow{top:46px;left:617px;display:flex;align-items:center;gap:6px;font-family:"Poppins",sans-serif;font-weight:600;font-size:14px;color:#333}
.soc{width:26px;height:26px;border-radius:50%}
.vbar{top:30px;left:838px;width:2px;height:56px;background:#ddd}
.call-ico{top:33px;left:866px;width:48px;height:48px;border-radius:50%;border:3px solid var(--blue)}
.call{top:36px;left:926px;font-family:"Poppins",sans-serif;color:#222}
.call small{display:block;font-size:13px;font-weight:600}
.call b{display:block;font-size:22px;font-weight:600}
.nav{top:118px;left:0;width:1200px;height:51px;background:var(--blue)}
.nav a{position:absolute;top:0;height:51px;line-height:51px;font-family:"Poppins",sans-serif;font-weight:600;font-size:13px;color:var(--white);text-decoration:none;transform:translateX(-50%)}
.nav a.active{background:var(--blue-dark);padding:0 22px}

/* hero */
.hero{top:169px;left:0;width:1200px;height:671px;background:linear-gradient(180deg,#6a6f93 0%,#c98aa0 30%,#d99aa6 45%,#6f5a70 65%,#3a2f3a 100%)}
.hero-title{top:340px;left:0;width:1200px;text-align:center;font-family:"Poppins",sans-serif;font-weight:700;font-size:68px;color:var(--white);text-shadow:0 3px 8px rgba(0,0,0,.35)}
.btn-light{top:437px;left:515px;width:170px;height:50px;background:var(--white);color:var(--blue);border:3px solid var(--white);box-shadow:0 0 0 4px rgba(255,255,255,.5)}
.hero-nav{top:476px;width:44px;height:44px;border-radius:50%;background:rgba(255,255,255,.25)}
.down{top:806px;left:569px;width:60px;height:60px;border-radius:50%;background:var(--white);box-shadow:0 2px 8px rgba(0,0,0,.2)}

/* services */
.svc{top:1043px;width:252px;text-align:center}
.svc-ring{margin:0 auto;width:248px;height:248px;border-radius:50%;border:4px solid var(--blue);padding:7px;background:var(--white)}
.svc-img{width:100%;height:100%;border-radius:50%}
.svc h3{margin-top:18px;font-family:"Poppins",sans-serif;font-weight:600;font-size:22px;line-height:26px;color:var(--ink)}

/* about */
.about{top:1440px;left:0;width:1200px;height:780px;background:var(--grey-bg)}
.about-photo{position:absolute;top:416px;left:0;width:1200px;height:364px;background:linear-gradient(180deg,#dfe3e2 0%,#8fa08f 25%,#3e523d 45%,#bfc6c4 62%,#7d8f86 100%)}
.about p{position:absolute;top:215px;left:160px;width:880px;text-align:center;font-size:13.5px;line-height:25.7px;color:#555}
.btn-blue{background:var(--blue);color:var(--white);box-shadow:0 0 0 3px var(--white),0 0 0 5px var(--blue)}

/* employment */
.job-photo{top:2402px;left:112px;width:483px;height:393px;border-radius:26px;border-right:12px solid var(--blue);background:linear-gradient(180deg,#c5d6ea 0%,#e4eaf2 40%,#4a6c92 55%,#34506d 100%)}
.job-row{position:absolute;left:621px;font-size:13.5px;line-height:25.7px}
.job-row .k{position:absolute;left:0;width:210px;font-family:"Poppins",sans-serif;font-weight:600;font-size:17px;color:var(--blue)}
.job-row .c{position:absolute;left:217px;color:var(--blue);font-weight:700}
.job-row .v{position:absolute;left:234px;width:270px;color:#555}

/* testimonials */
.testi{top:2870px;left:0;width:1200px;height:720px;background:linear-gradient(180deg,#1b4fb8 0%,#1f57c0 35%,#123a84 55%,#0e2c5c 75%,#16345c 100%)}
.card{top:3110px;width:306px;height:340px;border-radius:153px 153px 153px 153px/160px 160px 180px 180px;background:var(--white);border:4px solid var(--blue);text-align:center}
.quote{position:absolute;top:-28px;left:119px;width:60px;height:60px;border-radius:50%;background:var(--blue);border:4px solid var(--white);color:var(--white);font-family:"Poppins",sans-serif;font-weight:700;font-size:48px;line-height:70px}
.card p{position:absolute;top:74px;left:26px;width:246px;font-size:13.5px;line-height:25.7px;color:#555}
.card .who{position:absolute;top:245px;left:0;width:298px;font-family:"Poppins",sans-serif;font-weight:600;font-size:20px;color:var(--blue)}
.card .co{position:absolute;top:280px;left:0;width:298px;font-size:13px;color:#666}

/* gallery */
.shot{top:3767px;height:331px}
.handle{top:3910px;width:46px;height:46px;border-radius:50%;background:var(--white);box-shadow:0 1px 6px rgba(0,0,0,.3)}

/* footer */
.footer{top:4180px;left:0;width:1200px;height:556px;background:var(--footer);color:var(--white)}
.f-h{position:absolute;font-family:"Roboto",sans-serif;font-weight:500;font-size:17px;color:var(--white)}
.field{position:absolute;height:37px;background:var(--white);border:1px solid #ccc;font-size:12px;color:#555;padding:11px 18px}
.f-links a{position:absolute;left:670px;font-size:14px;color:var(--white);text-decoration:none}
.f-links span{position:absolute;left:650px;font-size:13px;color:var(--white)}
.f-contact{position:absolute;left:879px;font-size:14px;line-height:23px;color:var(--white)}
.f-rule{position:absolute;left:110px;top:460px;width:980px;height:1px;background:#333}
.copy{position:absolute;top:482px;left:0;width:1200px;text-align:center;font-size:14px;color:#ddd}
</style>
</head>
<body>

<!-- header -->
<div class="abs topline"></div>
<div class="abs brand">
  <div class="brand-name">Brightmoor</div>
  <div class="brand-tag">Shoreline care, season after season.</div>
</div>
<div class="abs follow">Follow us :
  <span class="soc" style="background:#3b5998"></span>
  <span class="soc" style="background:#1da1f2"></span>
  <span class="soc" style="background:#db4437"></span>
</div>
<div class="abs vbar"></div>
<div class="abs call-ico">
  <svg width="42" height="42" viewBox="0 0 42 42"><path d="M14 11c2 0 4 5 3 6l-2 2c1 3 4 6 7 7l2-2c1-1 6 1 6 3s-2 4-4 4C17 31 10 24 10 15c0-2 2-4 4-4z" fill="var(--blue)"/></svg>
</div>
<div class="abs call"><small>Call us Today :</small><b>+1 888 888 8888</b></div>

<nav class="abs nav">
  <a class="active" style="left:175px">HOME</a>
  <a style="left:274px">SERVICES</a>
  <a style="left:390px">ABOUT US</a>
  <a style="left:515px">CONTACT US</a>
  <a style="left:623px">FAQS</a>
  <a style="left:733px">EMPLOYMENT</a>
  <a style="left:880px">TESTIMONIALS</a>
  <a style="left:1009px">GALLERY</a>
</nav>

<!-- hero -->
<div class="abs hero" role="img" aria-label="Wooden dock with two wicker chairs on a calm lake at pink sunset, pine forest shore"></div>
<svg class="abs" style="top:700px;left:0" width="1200" height="145" viewBox="0 0 1200 145">
  <path d="M0 40 Q600 200 1200 40 L1200 145 L0 145 Z" fill="#fff"/>
  <path d="M0 44 Q600 204 1200 44" fill="none" stroke="var(--blue)" stroke-width="8"/>
</svg>
<div class="abs hero-title">Lake Weed Removal</div>
<div class="btn btn-light">GET STARTED &#10148;</div>
<div class="abs hero-nav" style="left:70px"></div>
<div class="abs hero-nav" style="left:1086px"></div>
<div class="abs down">
  <svg width="60" height="60" viewBox="0 0 60 60"><path d="M30 18v24M21 33l9 9 9-9" fill="none" stroke="var(--blue)" stroke-width="3" stroke-linecap="round"/></svg>
</div>

<!-- services -->
<h2 class="h2" style="top:928px">Our Services</h2>
<div class="rule" style="top:1011px"></div>
<svg class="arrow" style="top:1167px;left:40px" viewBox="0 0 30 30"><path d="M19 5 9 15l10 10" fill="none" stroke="#111" stroke-width="3"/></svg>
<svg class="arrow" style="top:1167px;left:1126px" viewBox="0 0 30 30"><path d="M11 5l10 10-10 10" fill="none" stroke="#111" stroke-width="3"/></svg>
<div class="abs svc" style="left:113px">
  <div class="svc-ring"><div class="svc-img" role="img" aria-label="Boat lift canopy frame on a dock over the lake" style="background:linear-gradient(180deg,#9cc0e6,#5d7fa6 60%,#355a7c)"></div></div>
  <h3>Dock Install and<br>Removal Services</h3>
</div>
<div class="abs svc" style="left:352px">
  <div class="svc-ring"><div class="svc-img" role="img" aria-label="Worker installing a canopy on a lakeside dock" style="background:linear-gradient(180deg,#a8cdf0,#3f6f9e 55%,#244b70)"></div></div>
  <h3>Canopy Services</h3>
</div>
<div class="abs svc" style="left:592px">
  <div class="svc-ring"><div class="svc-img" role="img" aria-label="Barge floating on a lake at sunset" style="background:linear-gradient(180deg,#c4d3e2,#e8b784 45%,#3b4e62 70%,#2a2f36)"></div></div>
  <h3>Barge Services<br>(Fall 2022)</h3>
</div>
<div class="abs svc" style="left:831px">
  <div class="svc-ring"><div class="svc-img" role="img" aria-label="Dock lift loaded on a red trailer" style="background:linear-gradient(180deg,#d8e1ea,#b7b7b7 50%,#7a3b3b 68%,#555)"></div></div>
  <h3>Dock Lift Services<br>(Fall 2022)</h3>
</div>

<!-- about -->
<section class="abs about">
  <div class="about-photo" role="img" aria-label="Misty lake at dawn with pine forest reflected in still water"></div>
  <svg class="abs" style="top:0;left:0" width="1200" height="780" viewBox="0 0 1200 780">
    <path d="M0 0 H1200 V95 Q600 -71 0 95 Z" fill="#fff"/>
    <path d="M0 95 Q600 -71 1200 95" fill="none" stroke="var(--blue)" stroke-width="8"/>
    <path d="M0 692 Q600 858 1200 692 V780 H0 Z" fill="#fff"/>
    <path d="M0 688 Q600 854 1200 688" fill="none" stroke="var(--blue)" stroke-width="10"/>
  </svg>
  <h2 class="h2" style="top:102px">About Us</h2>
  <div class="rule" style="top:188px"></div>
  <p>Brightmoor LLC is a company formed in response to the increase in invasive species in Minnesota lakes and waterways. The impact of these fast-growing nuisances inspired our venture to effectively control unwanted lake weeds and create an enjoyable environment craved by waterfront property homeowners.</p>
  <div class="btn btn-blue" style="top:322px;left:517px;width:166px;height:46px">LEARN MORE &#10148;</div>
</section>

<!-- employment -->
<h2 class="h2" style="top:2288px">Employment</h2>
<div class="rule" style="top:2372px"></div>
<div class="abs job-photo" role="img" aria-label="Boat lift with canopy frame at the end of a wooden dock"></div>
<div class="job-row" style="top:2409px"><span class="k">Job Title</span><span class="c">:</span><span class="v">Diver</span></div>
<div class="job-row" style="top:2461px"><span class="k">Compensation</span><span class="c">:</span><span class="v">Dependent upon qualifications.<br>HIRING NOW!</span></div>
<div class="job-row" style="top:2538px"><span class="k">About the Company</span><span class="c">:</span><span class="v">Brightmoor LLC offers shoreline management services to residential and commercial waterfront properties on lakes and waterways in the Twin Cities metro area. We have built a reputation on timeliness, quality, and convenience with chemical-free methods that produce lasting results. There is no life like lake life and we are dedicated to keeping it that way.</span></div>

<!-- testimonials -->
<section class="abs testi" role="img" aria-label="Evening lake with dark treeline and a dock under a deep blue sky">
  <svg class="abs" style="top:0;left:0" width="1200" height="720" viewBox="0 0 1200 720">
    <path d="M0 0 H1200 V79 Q600 -41 0 79 Z" fill="#fff"/>
    <path d="M0 62 Q600 -58 1200 62" fill="none" stroke="var(--blue)" stroke-width="8"/>
    <path d="M0 622 Q600 768 1200 622 V720 H0 Z" fill="#fff"/>
    <path d="M0 616 Q600 762 1200 616" fill="none" stroke="var(--blue)" stroke-width="10"/>
  </svg>
</section>
<h2 class="h2" style="top:2982px;color:var(--white)">Testimonials</h2>
<div class="rule" style="top:3067px;background:var(--white)"></div>
<svg class="arrow" style="top:3282px;left:40px" viewBox="0 0 30 30"><path d="M19 5 9 15l10 10" fill="none" stroke="#fff" stroke-width="3"/></svg>
<svg class="arrow" style="top:3282px;left:1126px" viewBox="0 0 30 30"><path d="M11 5l10 10-10 10" fill="none" stroke="#fff" stroke-width="3"/></svg>
<div class="abs card" style="left:110px">
  <div class="quote">&#8220;</div>
  <p>"Lorem ipsum dolor sit amet, consectetur adipiscing elit, sed do eiusmod tempor incididunt ut labore et dolore magna aliqua. Ut enim ad minim veniam, quis nostrud exercitation ulla commodo consequat."</p>
  <div class="who">John Doe</div><div class="co">Company name</div>
</div>
<div class="abs card" style="left:446px">
  <div class="quote">&#8220;</div>
  <p>"Lorem ipsum dolor sit amet, consectetur adipiscing elit, sed do eiusmod tempor incididunt ut labore et dolore magna aliqua. Ut enim ad minim veniam, quis nostrud exercitation ulla commodo consequat."</p>
  <div class="who">John Doe</div><div class="co">Company name</div>
</div>
<div class="abs card" style="left:781px">
  <div class="quote">&#8220;</div>
  <p>"Lorem ipsum dolor sit amet, consectetur adipiscing elit, sed do eiusmod tempor incididunt ut labore et dolore magna aliqua. Ut enim ad minim veniam, quis nostrud exercitation ulla commodo consequat."</p>
  <div class="who">John Doe</div><div class="co">Company name</div>
</div>

<!-- gallery -->
<h2 class="h2" style="top:3650px">Gallery</h2>
<div class="rule" style="top:3734px"></div>
<svg class="arrow" style="top:3918px;left:40px" viewBox="0 0 30 30"><path d="M19 5 9 15l10 10" fill="none" stroke="#111" stroke-width="3"/></svg>
<svg class="arrow" style="top:3918px;left:1126px" viewBox="0 0 30 30"><path d="M11 5l10 10-10 10" fill="none" stroke="#111" stroke-width="3"/></svg>
<div class="abs shot" style="left:119px;width:236px;background:linear-gradient(180deg,#9aa7ad,#7a6c4c 45%,#5b5440)" role="img" aria-label="Shoreline choked with lake weeds before removal"></div>
<div class="abs shot" style="left:355px;width:235px;background:linear-gradient(180deg,#b4c0c8,#6d7e88 40%,#4f5f68)" role="img" aria-label="Same shoreline with clear water after removal"></div>
<div class="abs handle" style="left:332px"><svg width="46" height="46" viewBox="0 0 46 46"><path d="M19 17l-6 6 6 6M27 17l6 6-6 6" fill="none" stroke="#222" stroke-width="2"/></svg></div>
<div class="abs shot" style="left:619px;width:235px;background:linear-gradient(180deg,#c9d2c4,#6e7a4a 45%,#59553d)" role="img" aria-label="Weed-covered dock walkway through reeds before cleanup"></div>
<div class="abs shot" style="left:854px;width:234px;background:linear-gradient(180deg,#cfd7d0,#7f8a5a 40%,#a89e8a 70%,#7a7262)" role="img" aria-label="Clean dock walkway through reeds after cleanup"></div>
<div class="abs handle" style="left:832px"><svg width="46" height="46" viewBox="0 0 46 46"><path d="M19 17l-6 6 6 6M27 17l6 6-6 6" fill="none" stroke="#222" stroke-width="2"/></svg></div>

<!-- footer -->
<footer class="abs footer">
  <svg class="abs" style="top:0;left:0" width="1200" height="100" viewBox="0 0 1200 100">
    <path d="M0 0 H1200 V84 Q600 -52 0 84 Z" fill="#fff"/>
    <path d="M0 76 Q600 -60 1200 76" fill="none" stroke="var(--blue)" stroke-width="8"/>
  </svg>
  <div class="f-h" style="top:142px;left:110px">GET IN TOUCH</div>
  <div class="field" style="top:190px;left:112px;width:233px">First Name</div>
  <div class="field" style="top:190px;left:353px;width:235px">Last Name</div>
  <div class="field" style="top:240px;left:112px;width:233px">Email</div>
  <div class="field" style="top:240px;left:353px;width:235px">phone number</div>
  <div class="field" style="top:290px;left:112px;width:476px;height:73px">Message</div>
  <div class="btn" style="top:379px;left:112px;width:132px;height:46px;background:var(--blue);color:#fff;font-size:14px">SUBMIT</div>

  <div class="f-h" style="top:142px;left:650px">QUICK LINKS</div>
  <div class="f-links">
    <span style="top:190px">&#187;</span><a style="top:190px">Home</a>
    <span style="top:219px">&#187;</span><a style="top:219px">Services</a>
    <span style="top:249px">&#187;</span><a style="top:249px">About Us</a>
    <span style="top:278px">&#187;</span><a style="top:278px">Contact Us</a>
    <span style="top:309px">&#187;</span><a style="top:309px">FAQs</a>
    <span style="top:339px">&#187;</span><a style="top:339px">Employment</a>
  </div>

  <div class="f-h" style="top:142px;left:847px">CONTACT US</div>
  <svg class="abs" style="top:196px;left:848px" width="14" height="18" viewBox="0 0 14 18"><path d="M7 1a6 6 0 0 1 6 6c0 4-6 10-6 10S1 11 1 7a6 6 0 0 1 6-6z" fill="var(--blue)"/><circle cx="7" cy="7" r="2" fill="#000"/></svg>
  <div class="f-contact" style="top:194px">Lorem ipsum dolor sit<br>amet, consectetur adip<br>iscing elit, sed</div>
  <svg class="abs" style="top:285px;left:849px" width="12" height="18" viewBox="0 0 12 18"><rect x="1" y="1" width="10" height="16" rx="2" fill="none" stroke="var(--blue)" stroke-width="2"/></svg>
  <div class="f-contact" style="top:284px">+1 888 888 8888</div>
  <svg class="abs" style="top:332px;left:847px" width="16" height="12" viewBox="0 0 16 12"><rect x="1" y="1" width="14" height="10" fill="none" stroke="var(--blue)" stroke-width="1.6"/><path d="M1 1l7 6 7-6" fill="none" stroke="var(--blue)" stroke-width="1.6"/></svg>
  <div class="f-contact" style="top:328px">info@companyname.com</div>

  <div class="f-h" style="top:400px;left:650px">STAY CONNECTED :</div>
  <span class="abs soc" style="top:397px;left:851px;background:var(--blue)"></span>
  <span class="abs soc" style="top:397px;left:891px;background:#c13584"></span>

  <div class="f-rule"></div>
  <div class="copy">© 2022 company Name &nbsp;| All Rights Reserved | Terms and Conditions</div>
</footer>

</body>
</html>
```